Buch-/eBook-Cover für Traumatherapeutin
Zielgruppe
Ich bin Traumatherapeutin und schreibe ein Buch zum Thema Trauma bearbeiten.
Meine Zielgruppe sucht Heilung, Genesung, Selbstliebe etc.
Aufgabenstellung
Buchcover
Bitte erstell mir ein modernes positives inspirierendes Buchcover mit dem
Titel: 'Morgenlicht NEU entdecken“
Untertitel: „Spüre den Mut der ganz in dir wohnt“
Dr. Mira Kessow
Ich hätte gerne ein modernes Buch, das entweder einen Bezug zum Thema Trauma hat oder aber einfach stylische Schriftzüge. Bin aber auch offen für andere Vorschläge.
Dunkelblau, weiß und türkis oder auch rosa mag ich ganz gerne. Wobei Dunkelblau, weiß und türkis meine Favoriten sind und mit rosa höchstens kleinere Akzente gesetzt werden sollten.
Das Buchcover soll modern sein und direkt ansprechen. Gerne eine originelle Lösung, oder etwas Besonderes, etwas das Tiefe ausdrückt, oder man mehrmals hinsehen muss um etwas zu erkennen oder etwas das mehr Interpretationsspielraum lässt.
Gerne auch viel weiß, zumindest heller und nicht zu dunkel. Stylish, aber nicht überfrachtet.
Schreib mich gerne an, wenn du Fragen hast.
Ich habe mal zwei Beispiel von Typolösungen angehängt, die ich ganz cool fände.
Ich freue mich auf deine Ideen :-)
Ganz liebe Grüße
Mira

```html
<!DOCTYPE html>
<html lang="de">
<head>
<meta charset="utf-8">
<title>Morgenlicht neu entdecken – Dr. Mira Kessow</title>
<link rel="stylesheet" href="https://fonts.googleapis.com/css2?family=Bebas+Neue&family=Kaushan+Script&family=Roboto:wght@400&display=swap">
<style>
  :root {
    --teal: #4fb9a5;
    --gold-light: #d2c13f;
    --gold-dark: #a68c18;
    --paper: #ffffff;
    --shell: #a07a4e;
    --sail: #eef0f1;
  }
  html, body {
    margin: 0;
    padding: 0;
    overflow: hidden;
    background: var(--paper);
  }
  .cover {
    position: relative;
    width: 750px;
    height: 1200px;
    background: var(--paper);
    overflow: hidden;
  }
  .author {
    position: absolute;
    top: 72px;
    left: 0;
    width: 100%;
    text-align: center;
    font-family: "Bebas Neue", sans-serif;
    font-size: 36px;
    letter-spacing: 0.5px;
    color: var(--teal);
    margin: 0;
  }
  .title {
    margin: 0;
    font-weight: normal;
  }
  .title-top,
  .title-bottom {
    position: absolute;
    left: 0;
    width: 100%;
    text-align: center;
    font-family: "Bebas Neue", sans-serif;
    color: var(--teal);
    line-height: 1;
    letter-spacing: 1px;
  }
  .title-top {
    top: 132px;
    font-size: 160px;
  }
  .title-bottom {
    top: 444px;
    font-size: 178px;
  }
  .title-accent {
    position: absolute;
    top: 212px;
    left: 0;
    width: 100%;
    text-align: center;
    font-family: "Kaushan Script", cursive;
    font-size: 220px;
    line-height: 1;
    background: linear-gradient(120deg, var(--gold-light) 15%, var(--gold-dark) 45%, var(--gold-light) 75%);
    -webkit-background-clip: text;
    background-clip: text;
    color: transparent;
  }
  .subtitle {
    position: absolute;
    top: 604px;
    left: 0;
    width: 100%;
    text-align: center;
    font-family: "Roboto", sans-serif;
    font-size: 34px;
    color: var(--teal);
    margin: 0;
  }
  .boat-image {
    position: absolute;
    left: 300px;
    top: 855px;
    width: 162px;
    height: 222px;
  }
</style>
</head>
<body>
  <main class="cover">
    <p class="author">Dr. Mira Kessow</p>
    <h1 class="title">
      <span class="title-top">Morgenlicht</span>
      <span class="title-bottom">Entdecken</span>
      <span class="title-accent">neu</span>
    </h1>
    <p class="subtitle">Spüre den Mut der ganz in dir wohnt</p>
    <svg class="boat-image" role="img" aria-label="Foto: kleines Boot aus einer Walnussschale mit weißem Papiersegel" viewBox="0 0 162 222">
      <defs>
        <linearGradient id="boatTone" x1="0" y1="0" x2="0" y2="1">
          <stop offset="0" stop-color="#f3f4f5"/>
          <stop offset="0.7" stop-color="#e6e2dc"/>
          <stop offset="1" stop-color="#b89570"/>
        </linearGradient>
      </defs>
      <rect width="162" height="222" rx="10" fill="url(#boatTone)"/>
    </svg>
  </main>
</body>
</html>
```